Women's Jewellery startup needs a captivating, beautifully designed and intuitive online store

[12/24 update]

Added 2 additional documents:

Feedback on designs received so far: designer feedback.docx
Product images from catalogue: products images.docx

Please read the feedback provided on designs provided so far to guide you further on your submission. The product images can be used to create promotional banners for the site.

@@@Added a document (VELISTO JEWELLERY_checklist.docx) which can be used by designers as a checklist when submitting their designs to ensure all aspects of the requirements have been covered @@@

+++IMPORTANT BUT NOT SPECIFIED IN THE REQUIREMENTS DOCUMENT - DESIGN SHOULD INCLUDE SUPPORT FOR MOBILE FRIENDLY SITE TOO+++

***Previous experience designing Jewellery online stores preferred (not essential)***

The name of the online Jewellery store is "Velisto Jewellery" and the business is based in Hong Kong. It will be run by 2 stay at home mothers. We need a Shopify themed store designed that will achieve the following objectives in order of priority:

• Conversion: The primary objective of the design/content is to prompt the customer to make a purchase. While this may sound obvious, it is mentioned so as not to distract the design process by focusing on other objectives (which are also important). The site also needs to be optimized so as to rank high in search engine searches for relevant keywords (SEO)
• Navigation: An intuitive interface which takes away a lot of the thinking from the customer by making it obvious what they need to do when they visit the store
• Engagement: Encourages the customer to spend time on the website and share content with their social network

Where applicable, the design of the store should reflect as closely as possible the mission statements and words outlined below:

• Jewellery you’ll fall in love with
• We want every client to leave the store with a smile
• We want to be able to provide the best service we can in every situation no matter what
• We aim to increase our business by word of mouth; therefore we tell people things about our store that makes it interesting for them to share
• We love every customer, no matter how difficult things get
• We, as a team, are so well informed about our products and brands that we always have the best information for our customers
• We celebrate women here!
• We celebrate life in here!
• We celebrate beauty here!
• We celebrate families here, as jewellery often stays within families.
• We will always try to make an extra step
• We will always try to exceed the expectation of our customers
• We will go as far as we possibly can to attract a customer back to our store and connect with us
• Every client that leaves our store knows more about jewellery because we passionately told him about it
• Romantic, classic, love, warm, cool, stylish

A draft functional specification is attached with this brief. We would like the design to reflect as closely as possible the functional requirements outlined in the document. Open to suggestions to improve upon the functional requirements.

Target Market(s)

Women aged 18-55

Industry/Entity Type

Jewelry Store

Coding

Coded - Design and coding required

Number of Pages Required

5+ page

Font styles to use
Other font styles liked:
• Myriad Pro as per Logo but open to any font that complements this one

Requirements
Must have
• 1. A look that encourages the user to make a purchase
• 2. An intuitive, easy to navigate and engaging interface
• 3. Primary colour scheme as defined in the functional specification attached
• 4. Simplistic look, not too cluttered
Nice to have
• 1. Closely matching the functional requirements of the site as outlined in the requirements specification but open to any better ideas

```html
<!DOCTYPE html>
<html lang="en">
<head>
<meta charset="utf-8">
<title>Velisto Jewellery</title>
<link rel="stylesheet" href="https://fonts.googleapis.com/css2?family=Poppins:wght@400;500;600&family=Open+Sans:wght@400;600&family=Tinos&display=swap">
<style>
:root{
  --black:#0b0b0b;
  --topbar:#121212;
  --gold:#c89a45;
  --gold-light:#e2b45a;
  --nav:#c5974a;
  --white:#ffffff;
  --text:#333333;
  --card-head:rgba(58,58,58,.9);
  --pill:#1d1d1d;
}
*{margin:0;padding:0;box-sizing:border-box}
html,body{width:1200px;height:3010px;overflow:hidden}
body{position:relative;background:var(--white);font-family:"Poppins",sans-serif;color:var(--text)}
.abs{position:absolute}

/* top bar */
.topbar{left:0;top:0;width:1200px;height:46px;background:var(--topbar);color:#ddd}
.topbar .phone{left:110px;top:12px;color:var(--gold-light);font-size:17px;display:flex;align-items:center;gap:8px}
.topbar .links{right:112px;top:14px;display:flex;gap:22px;font-size:13px;color:#e5e5e5}
.topbar .links span{display:flex;align-items:center;gap:6px}

/* header */
.header{left:0;top:46px;width:1200px;height:116px;background:var(--black)}
.promo{left:110px;top:10px;width:275px;height:94px;background:#161616;color:#fff;font-size:13px;line-height:19px;padding:14px 0 0 8px}
.promo b{color:var(--gold-light);font-weight:500}
.promo .gems{position:absolute;right:6px;top:6px;width:116px;height:82px;
  background:
    radial-gradient(circle at 30% 35%,#f4f4f4 0,#9a9a9a 14%,transparent 26%),
    radial-gradient(circle at 68% 30%,#ffffff 0,#a5a5a5 10%,transparent 20%),
    radial-gradient(circle at 58% 70%,#e6e6e6 0,#8a8a8a 12%,transparent 24%),
    radial-gradient(circle at 85% 72%,#dcdcdc 0,#777 9%,transparent 18%),
    #151515}
.brand{left:450px;top:14px;width:300px;text-align:center;color:var(--gold)}
.brand .mark{width:34px;height:34px;border:2px solid var(--gold);margin:0 auto 6px}
.brand .name{font-family:"Tinos",serif;font-size:24px;letter-spacing:6px;line-height:26px}
.brand .tag{font-family:"Tinos",serif;font-size:12px;letter-spacing:1.5px;color:#eee;margin-top:2px}
.cart{right:112px;top:10px;color:#eee;font-size:13px;display:flex;align-items:center;gap:8px}
.search{left:820px;top:58px;width:268px;height:34px;background:#2a2a2a;color:#ccc;font-size:12px;padding:9px 12px}
.search svg{position:absolute;right:10px;top:8px}

/* nav */
.nav{left:0;top:162px;width:1200px;height:40px;background:var(--nav)}
.nav ul{list-style:none;display:flex;position:absolute;left:112px;top:13px;font-size:12px;font-weight:500;color:#1b1b1b}
.nav li{margin-right:38px}
.nav .offers{position:absolute;left:970px;top:0;width:120px;height:40px;background:#d5a656;color:#fff;font-size:14px;font-weight:600;text-align:center;line-height:40px}

/* hero */
.hero{left:0;top:202px;width:1200px;height:470px;
  background:
    radial-gradient(ellipse 260px 220px at 1120px 330px,rgba(70,60,45,.35),transparent 70%),
    linear-gradient(90deg,#1c1c1c 0%,#2f2f2f 28%,#1e1e1e 58%,#0a0a0a 100%)}
.hero .photo{left:0;top:0;width:720px;height:470px;
  background:
    radial-gradient(ellipse 40px 60px at 430px 370px,rgba(255,255,255,.75),transparent 70%),
    radial-gradient(ellipse 170px 120px at 360px 230px,rgba(240,240,240,.9),rgba(190,190,190,.55) 45%,transparent 75%),
    radial-gradient(ellipse 260px 210px at 380px 260px,rgba(120,120,120,.55),transparent 75%),
    radial-gradient(ellipse 200px 260px at 380px 60px,#3a3a3a,transparent 80%),
    linear-gradient(180deg,#262626,#151515)}
.hero h1{left:740px;top:140px;width:350px;text-align:center;font-family:"Tinos",serif;font-weight:400;font-size:40px;letter-spacing:6px;color:#fff}
.hero .sub{left:740px;top:190px;width:350px;text-align:center;font-family:"Tinos",serif;font-size:17px;letter-spacing:2px;color:var(--gold-light)}
.hero p{left:740px;top:222px;width:350px;text-align:center;font-size:12px;line-height:20px;color:#bbb}
.hero .btn{left:862px;top:288px;width:106px;height:44px;border:1px dashed var(--gold);color:#fff;font-size:11px;font-weight:500;display:flex;align-items:center;justify-content:center;gap:6px}
.dots{left:560px;top:440px;display:flex;gap:8px}
.dots i{width:11px;height:11px;border-radius:50%;border:1.5px solid var(--gold);display:block}
.dots i.on{background:var(--gold)}

/* categories */
.cats{left:0;top:672px;width:1200px;height:344px;background:linear-gradient(180deg,#141414,#0c0c0c)}
.section-title{width:1200px;left:0;text-align:center;font-family:"Tinos",serif;font-weight:400;font-size:32px;color:var(--gold);letter-spacing:.5px}
.cat{top:120px;width:140px;text-align:center;color:#fff;font-size:15px}
.cat .disc{width:130px;height:130px;border-radius:50%;background:#1c1c1c;border:1px solid #262626;margin:0 auto 20px;display:flex;align-items:center;justify-content:center}

/* difference */
.diff p.lead{left:140px;top:124px;width:920px;text-align:center;font-size:11.5px;line-height:24px;color:#333}
.list{list-style:none;font-size:11.5px;line-height:16px;color:#333;width:400px}
.list li{position:relative;padding-left:24px;margin-bottom:10px}
.list li svg{position:absolute;left:0;top:3px}

/* promo banner */
.banner{left:0;top:1538px;width:1200px;height:384px;overflow:hidden;
  background:
    radial-gradient(ellipse 420px 120px at 600px 60px,rgba(255,235,160,.35),transparent 75%),
    linear-gradient(160deg,#b8912e 0%,#d9b64e 38%,#cda541 62%,#a57f22 100%)}
.banner .art{position:absolute}
.banner .kicker{left:0;top:92px;width:1200px;text-align:center;font-family:"Tinos",serif;font-size:31px;color:#1b1b1b;letter-spacing:1px}
.banner h2{left:0;top:126px;width:1200px;text-align:center;font-family:"Tinos",serif;font-weight:400;font-size:44px;color:#111;letter-spacing:1px}
.banner .tagline{left:0;top:198px;width:1200px;text-align:center;font-family:"Tinos",serif;font-size:15px;color:#2a2a2a;letter-spacing:1px}
.pills{left:0;top:252px;width:1200px;display:flex;justify-content:center;gap:12px}
.pills span{background:var(--pill);color:#fff;font-size:11px;font-weight:500;border-radius:14px;padding:6px 14px}

/* catalogue */
.card{overflow:hidden}
.card .head{position:absolute;left:0;top:0;width:100%;height:48px;background:var(--card-head);color:#fff;font-family:"Open Sans",sans-serif;font-size:19px;text-align:center;line-height:48px;z-index:1}
.card .img{position:absolute;inset:0}

/* footer */
.footer{left:0;top:2736px;width:1200px;height:274px;background:var(--black);color:#ddd}
.footer h4{font-family:"Open Sans",sans-serif;font-weight:600;font-size:15px;color:#fff;margin-bottom:6px}
.footer .col{top:32px;font-size:13px;line-height:23px}
.footer .news p{font-size:12px;line-height:20px;width:400px}
.footer .input{left:686px;top:112px;width:292px;height:44px;background:#fff;color:#888;font-size:11px;padding:15px 14px}
.footer .sub{left:978px;top:112px;width:110px;height:44px;background:var(--gold);color:#fff;font-size:14px;font-weight:600;text-align:center;line-height:44px}
.footer .rule{left:0;top:192px;width:1200px;height:1px;background:#222}
.social{left:110px;top:216px;display:flex;gap:12px}
.social i{width:30px;height:30px;border-radius:50%;background:var(--gold-light);display:block}
.copy{right:112px;top:222px;font-size:12px;color:#ccc}
</style>
</head>
<body>

<div class="abs topbar">
  <div class="abs phone">
    <svg width="16" height="16" viewBox="0 0 24 24" fill="currentColor"><path d="M6.6 10.8a15 15 0 006.6 6.6l2.2-2.2a1 1 0 011-.25 11.4 11.4 0 003.6.57 1 1 0 011 1V20a1 1 0 01-1 1A17 17 0 013 4a1 1 0 011-1h3.5a1 1 0 011 1c0 1.25.2 2.45.57 3.6a1 1 0 01-.25 1z"/></svg>
    (012) 555 0142
  </div>
  <div class="abs links">
    <span><svg width="13" height="12" viewBox="0 0 24 22" fill="#e2b45a"><path d="M12 21l-1.5-1.3C5 15 2 12.2 2 8.5 2 5.4 4.4 3 7.5 3c1.7 0 3.4.8 4.5 2.1C13.1 3.8 14.8 3 16.5 3 19.6 3 22 5.4 22 8.5c0 3.7-3 6.5-8.5 11.2z"/></svg>Wishlist</span>
    <span><svg width="12" height="13" viewBox="0 0 24 24" fill="#e2b45a"><circle cx="12" cy="7" r="5"/><path d="M2 23c0-6 4.5-9 10-9s10 3 10 9z"/></svg>Sign in</span>
    <span><svg width="13" height="12" viewBox="0 0 24 22" fill="#e2b45a"><rect x="2" y="3" width="20" height="5"/><rect x="2" y="10" width="20" height="5"/><rect x="2" y="17" width="20" height="5"/></svg>Currency: <b style="color:#fff;font-weight:600">HKD</b> ▾</span>
  </div>
</div>

<div class="abs header">
  <div class="abs promo">
    Extra <b>10% OFF</b> for orders<br>over <b>$500</b> till<br>March 31st, 2018*
    <div class="gems" role="img" aria-label="Loose diamonds on black"></div>
  </div>
  <div class="abs brand">
    <div class="mark"></div>
    <div class="name">VELISTO</div>
    <div class="tag">JEWELLERY YOU'LL FALL IN LOVE WITH</div>
  </div>
  <div class="abs cart">
    <svg width="14" height="14" viewBox="0 0 24 24" fill="#e2b45a"><path d="M4 8h16l-1.5 14h-13zM8 8a4 4 0 018 0h-2a2 2 0 00-4 0z"/></svg>
    (0) Items in Cart
  </div>
  <div class="abs search">Search
    <svg width="16" height="16" viewBox="0 0 24 24" fill="none" stroke="#e2b45a" stroke-width="2.5"><circle cx="10" cy="10" r="7"/><path d="M15 15l6 6"/></svg>
  </div>
</div>

<nav class="abs nav">
  <ul>
    <li>ABOUT</li><li>RINGS ▾</li><li>BRACELETS ▾</li><li>NECKLACES ▾</li><li>CHARMS ▾</li><li>EARRINGS ▾</li><li>BY MATERIAL ▾</li><li>CONTACT</li>
  </ul>
  <div class="offers">OFFERS</div>
</nav>

<section class="abs hero">
  <div class="abs photo" role="img" aria-label="Diamond necklace displayed on a black velvet bust"></div>
  <h1 class="abs">JEWELLERY</h1>
  <div class="abs sub">FOR ALL OCCASIONS</div>
  <p class="abs">Lorem ipsum dolor sit amet, consectetuer adipiscing elit, sed diam nonummy nibh euismod tincidunt.</p>
  <div class="abs btn">SHOP NOW <span style="font-size:9px">▶</span></div>
  <div class="abs dots"><i class="on"></i><i></i><i></i><i></i></div>
</section>

<section class="abs cats">
  <h2 class="abs section-title" style="top:58px">SHOP BY CATEGORY</h2>
  <div class="abs cat" style="left:126px">
    <div class="disc"><svg width="70" height="50" viewBox="0 0 70 50" fill="none" stroke="#ddd" stroke-width="3"><circle cx="25" cy="25" r="18"/><circle cx="45" cy="25" r="18"/></svg></div>EARRINGS</div>
  <div class="abs cat" style="left:326px">
    <div class="disc"><svg width="70" height="60" viewBox="0 0 70 60" fill="none" stroke="#ddd" stroke-width="3"><circle cx="25" cy="36" r="17"/><circle cx="45" cy="36" r="17"/><path d="M40 14l5-6 5 6-5 5z"/></svg></div>RINGS</div>
  <div class="abs cat" style="left:528px">
    <div class="disc"><svg width="70" height="50" viewBox="0 0 70 50" fill="none" stroke="#ddd" stroke-width="4"><ellipse cx="35" cy="25" rx="28" ry="10" transform="rotate(-20 35 25)"/></svg></div>BRACELETS</div>
  <div class="abs cat" style="left:730px">
    <div class="disc"><svg width="70" height="60" viewBox="0 0 70 60" fill="none" stroke="#ddd" stroke-width="3"><path d="M8 8q27 40 54 0"/><path d="M28 38h14l-7 12z" fill="#ddd"/></svg></div>NECKLACES</div>
  <div class="abs cat" style="left:930px">
    <div class="disc"><svg width="60" height="66" viewBox="0 0 60 66" fill="none" stroke="#ddd" stroke-width="3"><circle cx="30" cy="8" r="5"/><path d="M22 18h16l10 10v16l-10 10H22L12 44V28z"/><path d="M25 24h10l7 7v10l-7 7H25l-7-7V31z"/></svg></div>CHARMS</div>
</section>

<section class="abs diff" style="left:0;top:1016px;width:1200px;height:522px">
  <h2 class="abs section-title" style="top:58px">THE VELISTO DIFFERENCE</h2>
  <p class="abs lead">Lorem ipsum dolor sit amet, consectetuer adipiscing elit, sed diam nonummy nibh euismod tincidunt ut laoreet dolore magna aliquam erat volutpat. Ut wisi enim ad minim veniam, quis nostrud exerci tation ullamcorper suscipit lobortis nisl ut aliquip ex ea commodo consequat. Duis autem vel eum iriure dolor in hendrerit in vulputate velit esse molestie consequat, vel illum dolore eu feugiat nulla.</p>
  <ul class="abs list" style="left:110px;top:214px">
    <li><svg width="12" height="10" viewBox="0 0 12 10" fill="#c89a45"><path d="M0 3l3-3h6l3 3-6 7z"/></svg>Jewellery you'll fall in love with</li>
    <li><svg width="12" height="10" viewBox="0 0 12 10" fill="#c89a45"><path d="M0 3l3-3h6l3 3-6 7z"/></svg>We want every client to leave the store with a smile</li>
    <li><svg width="12" height="10" viewBox="0 0 12 10" fill="#c89a45"><path d="M0 3l3-3h6l3 3-6 7z"/></svg>We want to be able to provide the best service we can in every situation no matter what</li>
    <li><svg width="12" height="10" viewBox="0 0 12 10" fill="#c89a45"><path d="M0 3l3-3h6l3 3-6 7z"/></svg>We aim to increase our business by word of mouth; therefore we tell people things about our store that makes it interesting for them to share</li>
    <li><svg width="12" height="10" viewBox="0 0 12 10" fill="#c89a45"><path d="M0 3l3-3h6l3 3-6 7z"/></svg>We only want Fairtrade jewellery and we have strong values on humanitarian issues</li>
    <li><svg width="12" height="10" viewBox="0 0 12 10" fill="#c89a45"><path d="M0 3l3-3h6l3 3-6 7z"/></svg>We love every customer, no matter how difficult things get</li>
    <li><svg width="12" height="10" viewBox="0 0 12 10" fill="#c89a45"><path d="M0 3l3-3h6l3 3-6 7z"/></svg>We, as a team, are so well informed about our products and brands that we always have the best information for our customers</li>
  </ul>
  <ul class="abs list" style="left:562px;top:214px;width:520px">
    <li><svg width="12" height="10" viewBox="0 0 12 10" fill="#c89a45"><path d="M0 3l3-3h6l3 3-6 7z"/></svg>We celebrate women here!</li>
    <li><svg width="12" height="10" viewBox="0 0 12 10" fill="#c89a45"><path d="M0 3l3-3h6l3 3-6 7z"/></svg>We celebrate life in here!</li>
    <li><svg width="12" height="10" viewBox="0 0 12 10" fill="#c89a45"><path d="M0 3l3-3h6l3 3-6 7z"/></svg>We celebrate beauty here!</li>
    <li><svg width="12" height="10" viewBox="0 0 12 10" fill="#c89a45"><path d="M0 3l3-3h6l3 3-6 7z"/></svg>We celebrate families here, as jewellery often stays within families.</li>
    <li><svg width="12" height="10" viewBox="0 0 12 10" fill="#c89a45"><path d="M0 3l3-3h6l3 3-6 7z"/></svg>We will always try to make an extra step</li>
    <li><svg width="12" height="10" viewBox="0 0 12 10" fill="#c89a45"><path d="M0 3l3-3h6l3 3-6 7z"/></svg>We will always try to exceed the expectation of our customers</li>
    <li><svg width="12" height="10" viewBox="0 0 12 10" fill="#c89a45"><path d="M0 3l3-3h6l3 3-6 7z"/></svg>We will go as far as we possibly can to attract a customer back to our store and connect with us</li>
    <li><svg width="12" height="10" viewBox="0 0 12 10" fill="#c89a45"><path d="M0 3l3-3h6l3 3-6 7z"/></svg>Every client that leaves our store knows more about jewellery because we passionately told him about it</li>
    <li><svg width="12" height="10" viewBox="0 0 12 10" fill="#c89a45"><path d="M0 3l3-3h6l3 3-6 7z"/></svg>Romantic, classic, love, warm, cool, stylish</li>
  </ul>
</section>

<section class="abs banner">
  <div class="art" style="left:0;top:0;width:320px;height:384px;background:radial-gradient(ellipse 95px 110px at 150px 175px,rgba(246,205,170,.95),rgba(190,120,80,.75) 50%,transparent 80%),radial-gradient(ellipse 180px 60px at 260px 320px,rgba(200,30,40,.7),transparent 75%)" role="img" aria-label="Rose gold ring pendant on a chain beside a red ribbon"></div>
  <div class="art" style="left:860px;top:100px;width:340px;height:284px;background:radial-gradient(ellipse 80px 75px at 100px 140px,rgba(248,220,190,.95),rgba(200,140,95,.7) 50%,transparent 80%),radial-gradient(ellipse 80px 75px at 250px 170px,rgba(248,220,190,.95),rgba(200,140,95,.7) 50%,transparent 80%)" role="img" aria-label="Rose gold flower drop earrings"></div>
  <div class="abs kicker">PROMOTIONAL</div>
  <h2 class="abs">VARIATIONS OF PASSAGES</h2>
  <div class="abs tagline">MAJORITY HAVE SUFFERED ALTERATION IN SOME FORM, BY INJECTED HUMOUR</div>
  <div class="abs pills"><span>EARRINGS</span><span>RINGS</span><span>BRACELETS</span><span>NECKLACES</span><span>CHARMS</span></div>
</section>

<section class="abs" style="left:0;top:1922px;width:1200px;height:814px">
  <h2 class="abs section-title" style="top:58px">PRODUCT CATALOGUE</h2>
  <div class="abs card" style="left:110px;top:142px;width:472px;height:292px">
    <div class="head">DIAMOND JEWELLERY</div>
    <div class="img" role="img" aria-label="Diamond bracelet with an emerald ring" style="background:radial-gradient(ellipse 90px 60px at 320px 170px,#1e8a4e,rgba(20,110,60,.6) 55%,transparent 85%),radial-gradient(ellipse 160px 70px at 170px 150px,rgba(250,250,250,.9),transparent 80%),linear-gradient(180deg,#e4e4e4,#b9bebc 70%,#8c9290)"></div>
  </div>
  <div class="abs card" style="left:616px;top:142px;width:472px;height:292px">
    <div class="head">ROSE GOLD JEWELLERY</div>
    <div class="img" role="img" aria-label="Rose gold rose pendant necklace on blue" style="background:radial-gradient(ellipse 45px 90px at 236px 200px,rgba(240,170,140,.9),rgba(210,140,110,.4) 55%,transparent 85%),linear-gradient(160deg,#557aa0,#3a5a7c)"></div>
  </div>
  <div class="abs card" style="left:110px;top:466px;width:306px;height:264px">
    <div class="head">PLATINUM JEWELLERY</div>
    <div class="img" role="img" aria-label="Platinum wedding bands" style="background:radial-gradient(ellipse 120px 45px at 150px 170px,#ffffff,rgba(200,200,200,.5) 60%,transparent 85%),linear-gradient(180deg,#f0f0f0,#bcbcbc)"></div>
  </div>
  <div class="abs card" style="left:446px;top:466px;width:306px;height:264px">
    <div class="head">GEMSTONE JEWELLERY</div>
    <div class="img" role="img" aria-label="Enamel and gemstone rings" style="background:radial-gradient(ellipse 60px 50px at 60px 110px,rgba(40,150,120,.8),transparent 85%),radial-gradient(ellipse 80px 90px at 160px 160px,rgba(230,230,230,.9),transparent 80%),linear-gradient(160deg,#6c7a86,#a9aeb3 60%,#8a8c91)"></div>
  </div>
  <div class="abs card" style="left:782px;top:466px;width:306px;height:264px">
    <div class="head">GOLD PLATED JEWELLERY</div>
    <div class="img" role="img" aria-label="Gold plated ring with small stones" style="background:radial-gradient(ellipse 100px 60px at 160px 150px,rgba(232,178,60,.95),rgba(190,140,50,.5) 60%,transparent 85%),linear-gradient(160deg,#8a9098,#b8b2a0 60%,#9a8a5a)"></div>
  </div>
</section>

<footer class="abs footer">
  <div class="abs col" style="left:110px"><h4>ABOUT US</h4>Our Story<br>Wholesale inquiries</div>
  <div class="abs col" style="left:300px"><h4>SHOPPING</h4>Orders<br>Wishlist<br>Size Guide</div>
  <div class="abs col" style="left:446px"><h4>CUSTOMER CARE</h4>Returns<br>FAQs<br>Care &amp; Warranty<br>Contact Us</div>
  <div class="abs col news" style="left:686px"><h4>NEWSLETTER SIGNUP</h4><p>Lorem ipsum dolor sit amet, consectetuer adipiscing elit, sed diam nonummy nibh euismod tincidunt.</p></div>
  <div class="abs input">Enter Your Mail Id</div>
  <div class="abs sub">SUBSCRIBE</div>
  <div class="abs rule"></div>
  <div class="abs social"><i aria-hidden="true"></i><i aria-hidden="true"></i><i aria-hidden="true"></i></div>
  <div class="abs copy">© All Rights Reserved</div>
</footer>

</body>
</html>
```